Business Card Design needed for start up company Halvora

In need of a new business card designed for a start up company based in Sydney, Halvora is a new start up innovative Company, our mission it to make property accessible for everyday Australian and to become the leading Real Estate platform in Australia. We want it to be fresh and clean.

Industry/Entity Type

Financial

Contact Information for Business Card

Section for Name
Section for Title

HALVORA - The Strength of Pooling
Mobile:
Direct:

Font styles to use
Sans Serif

Colors
33a6d7
0692cd
0255a3
ffffff

Requirements
Must have
• Logo, all business card details

```html
<!DOCTYPE html>
<html lang="en">
<head>
<meta charset="utf-8">
<title>Halvora Business Card</title>
<link href="https://fonts.googleapis.com/css2?family=Montserrat:ital,wght@0,300;0,400;0,600;0,800;1,400&display=swap" rel="stylesheet">
<style>
  :root {
    --navy: #1f4585;
    --deep-blue: #0255a3;
    --sky: #33a6d7;
    --bright-blue: #0692cd;
    --white: #ffffff;
    --paper: #f4f5f6;
    --ink: #3d4550;
    --stage: #e6e8eb;
  }
  * { box-sizing: border-box; margin: 0; padding: 0; }
  html, body { width: 1200px; height: 911px; overflow: hidden; }
  body {
    background: var(--stage);
    font-family: "Montserrat", sans-serif;
    position: relative;
  }
  .card {
    position: absolute;
    top: 300px;
    width: 540px;
    height: 310px;
    border-radius: 18px;
    overflow: hidden;
    box-shadow: 0 6px 18px rgba(0,0,0,0.18);
  }
  .card-front { left: 45px; background: var(--paper); }
  .card-back { left: 615px; background: var(--navy); }

  .front-arcs { position: absolute; inset: 0; }

  .brand {
    position: absolute;
    display: flex;
    align-items: center;
    gap: 10px;
  }
  .brand-dot { border-radius: 50%; flex: none; }
  .brand-name { font-weight: 800; letter-spacing: 0.5px; line-height: 1; }

  .card-front .brand { left: 40px; top: 108px; }
  .card-front .brand-dot { width: 44px; height: 44px; background: var(--sky); }
  .card-front .brand-name { font-size: 40px; color: var(--deep-blue); }

  .person {
    position: absolute;
    right: 150px;
    top: 52px;
    text-align: right;
  }
  .person-name { font-weight: 800; font-size: 17px; color: var(--deep-blue); }
  .person-title { font-weight: 400; font-size: 13px; color: var(--sky); letter-spacing: 0.5px; margin-top: 2px; }

  .contact {
    position: absolute;
    left: 96px;
    top: 180px;
    font-size: 11.5px;
    font-weight: 400;
    color: var(--ink);
    line-height: 1.5;
  }
  .contact-address { margin-bottom: 4px; }
  .contact-line { display: flex; align-items: center; gap: 7px; }
  .contact-line svg { width: 10px; height: 10px; flex: none; }

  .card-back .brand { left: 190px; top: 98px; }
  .card-back .brand-dot { width: 56px; height: 56px; background: var(--white); }
  .card-back .brand-name { font-size: 48px; color: var(--white); }
  .tagline {
    position: absolute;
    left: 60px;
    bottom: 46px;
    font-style: italic;
    font-size: 13px;
    color: var(--white);
    letter-spacing: 0.3px;
  }
</style>
</head>
<body>
  <section class="card card-front">
    <svg class="front-arcs" viewBox="0 0 540 310" width="540" height="310" aria-hidden="true">
      <rect width="540" height="310" fill="var(--navy)"/>
      <path d="M390,0 C480,40 525,160 505,310 L0,310 L0,0 Z" fill="var(--sky)"/>
      <path d="M340,0 C430,50 470,170 440,310" fill="none" stroke="var(--white)" stroke-width="10"/>
      <path d="M335,0 C425,50 463,170 433,310 L0,310 L0,0 Z" fill="var(--paper)"/>
    </svg>

    <div class="brand">
      <span class="brand-dot"></span>
      <span class="brand-name">HALVORA</span>
    </div>

    <div class="person">
      <div class="person-name">MARA ELLISON</div>
      <div class="person-title">CEO/FOUNDER</div>
    </div>

    <div class="contact">
      <div class="contact-address">412 Harbour Street<br>Sydney, NSW 2000</div>
      <div class="contact-line">
        <svg viewBox="0 0 10 10"><path d="M2 0.5 L4 2.5 L3 3.8 C3.8 5.4 4.6 6.2 6.2 7 L7.5 6 L9.5 8 L8 9.5 C4 9 1 6 0.5 2 Z" fill="var(--navy)"/></svg>
        <span>612 480 3175</span>
      </div>
      <div class="contact-line">
        <svg viewBox="0 0 10 10"><rect x="2.5" y="0.5" width="5" height="9" rx="1" fill="none" stroke="var(--navy)" stroke-width="1.2"/></svg>
        <span>614 902 5583</span>
      </div>
      <div class="contact-line">
        <svg viewBox="0 0 10 10"><rect x="0.5" y="2" width="9" height="6.5" fill="var(--navy)"/><path d="M0.5 2 L5 5.5 L9.5 2" fill="none" stroke="var(--white)" stroke-width="0.9"/></svg>
        <span>mara@halvora.com</span>
      </div>
      <div class="contact-line">
        <svg viewBox="0 0 10 10"><circle cx="5" cy="5" r="4.5" fill="var(--navy)"/><path d="M0.5 5 H9.5 M5 0.5 C2.5 3 2.5 7 5 9.5 M5 0.5 C7.5 3 7.5 7 5 9.5" fill="none" stroke="var(--white)" stroke-width="0.7"/></svg>
        <span>www.halvora.com</span>
      </div>
    </div>
  </section>

  <section class="card card-back">
    <div class="brand">
      <span class="brand-dot"></span>
      <span class="brand-name">HALVORA</span>
    </div>
    <p class="tagline">The Strength of Pooling</p>
  </section>
</body>
</html>
```